Talvoro bonds (Surety bond broker)

We are a broker of surety bonds, we need a presentation and a flyer with fresh design. Our core values are reliable, on time and customized service. We want to transmit to our clients, they can leave on us the process of underwriting and issuing a surety bond, so they can focus on their business with no distractions.

Font styles to use
Sans Serif
Other font styles liked:

Requirements
Must have
• Visually attractive.
Main Message: Fast service issuing and underwriting surety bonds, reliable, nos surprises, we are always one step ahead, customized and personalized bonding solutions.
Nice to have
• Have short version for the flyer, and extended version for the presentation.
Should not have
• We already have a logo (attached), maintain colors

```html
<!DOCTYPE html>
<html lang="es">
<head>
<meta charset="utf-8">
<title>Talvoro bonds – Folleto</title>
<link href="https://fonts.googleapis.com/css2?family=Montserrat:wght@400;600;700;800&family=Open+Sans:wght@400;600&display=swap" rel="stylesheet">
<style>
:root{
  --green:#72b62f;
  --green-dark:#4f8a1c;
  --charcoal:#2f3033;
  --charcoal-2:#3b3d41;
  --ink:#4a4a4a;
  --paper:#ffffff;
  --mist:#f1f2f0;
  --backdrop:#9a9c9f;
}
*{box-sizing:border-box;margin:0;padding:0}
html,body{width:853px;height:1200px;overflow:hidden;background:var(--backdrop)}
body{position:relative;font-family:"Open Sans",Arial,sans-serif;color:var(--ink)}
.sheet{position:absolute;left:30px;width:793px;height:565px;display:flex;box-shadow:0 4px 14px rgba(0,0,0,.35);overflow:hidden}
.sheet--outside{top:18px}
.sheet--inside{top:612px;background:var(--charcoal)}
.panel{position:relative;width:264.33px;height:100%;overflow:hidden}
h2,h3,h4{font-family:"Montserrat",Arial,sans-serif}
.photo{position:absolute}
p.small{font-size:7.4px;line-height:1.5;margin-bottom:7px}

/* outside: about */
.about{background:var(--paper);padding:26px 22px}
.about h2{font-size:17px;color:var(--charcoal);font-weight:700;margin-bottom:12px}
.about h2 span{color:var(--green)}
.about .photo{left:0;bottom:0;width:100%;height:175px;background:linear-gradient(160deg,#c9d3dc,#7d8a96 55%,#4c5560)}

/* outside: clients & contact */
.clients{background:var(--charcoal);padding:22px 20px;color:#fff}
.clients h3{font-size:11px;color:var(--green);text-align:center;margin-bottom:10px}
.partner-board{background:#fff;border-radius:4px;padding:12px;display:grid;grid-template-columns:1fr 1fr;gap:10px 14px}
.partner-badge{height:20px;border-radius:3px;background:#d7dbd9}
.partner-badge:nth-child(3n+1){background:#c5d9b2}
.curve{position:absolute;left:-130px;top:255px;width:260px;height:260px;border-radius:50%;border:10px solid var(--green);background:#fff}
.contact{position:absolute;left:118px;top:268px;right:14px}
.contact h4{font-size:13px;color:#fff;margin-bottom:10px}
.contact-row{display:flex;gap:6px;align-items:flex-start;margin-bottom:9px;font-size:7px;line-height:1.45;color:#ddd}
.contact-row b{color:var(--green);font-weight:600;display:block}
.contact-row svg{flex:0 0 12px}
.site{position:absolute;bottom:14px;left:0;right:0;text-align:center;font-size:8px;color:#ccc}
.site b{color:var(--green)}

/* outside: cover */
.cover{background:var(--charcoal)}
.brand{position:absolute;top:40px;left:0;right:0;display:flex;align-items:center;justify-content:center;gap:8px;color:#fff;font-family:"Montserrat",Arial,sans-serif;font-weight:700;font-size:24px;letter-spacing:1px}
.brand i{width:14px;height:14px;border-radius:50%;background:var(--green);display:block}
.brand-sub{position:absolute;top:74px;left:0;right:0;text-align:center;font-size:7px;letter-spacing:2px;color:#bbb}
.cover .photo{top:130px;left:0;width:100%;height:250px;border-radius:120px 0 0 0;background:linear-gradient(200deg,#c8cfd4,#8e9aa3 50%,#5d6770)}
.tagline{position:absolute;top:405px;left:24px;font-family:"Montserrat",Arial,sans-serif;font-size:20px;font-weight:700;color:#fff;line-height:1.15}
.tagline span{color:var(--green)}
.social{position:absolute;top:470px;left:24px;right:24px;display:flex;gap:6px;align-items:center;font-size:7px;color:#bbb}
.social i{width:9px;height:9px;border-radius:50%;background:var(--green);display:block}

/* inside */
.inside-photo{position:absolute;top:0;left:0;width:100%;height:210px;background:linear-gradient(180deg,#8b949b,#5a6168 60%,var(--charcoal))}
.inside-col{position:relative;padding:222px 20px 0;color:#ddd}
.inside-col h3{font-size:13px;color:#fff;font-weight:700;margin-bottom:8px}
.inside-col h3::after{content:"";display:block;width:34px;height:3px;background:var(--green);margin-top:5px}
.inside-col ul{list-style:none;font-size:7.2px;line-height:1.5}
.inside-col li{padding-left:9px;position:relative;margin-bottom:4px}
.inside-col li::before{content:"";position:absolute;left:0;top:4px;width:4px;height:4px;background:var(--green);border-radius:50%}
.products-col{padding-top:150px}
.product-row{display:flex;gap:10px;align-items:flex-start;margin-bottom:16px}
.icon-disc{flex:0 0 44px;height:44px;border-radius:50%;background:var(--green);display:flex;align-items:center;justify-content:center}
.special{background:var(--mist);color:var(--ink);padding:150px 20px 0}
.special h3{color:var(--charcoal)}
.special h4{font-size:9px;color:var(--green-dark);margin:10px 0 3px}
.special p{font-size:7px;line-height:1.45}
.cta{position:absolute;left:20px;right:20px;bottom:22px;background:var(--green);color:#fff;text-align:center;padding:8px 0;border-radius:3px;font-family:"Montserrat",Arial,sans-serif}
.cta strong{display:block;font-size:15px;letter-spacing:1px}
.cta span{font-size:10px;font-weight:600}
</style>
</head>
<body>

<section class="sheet sheet--outside">
  <div class="panel about">
    <h2>¿Quiénes <span>somos?</span></h2>
    <p class="small">Talvoro bonds es un grupo de agentes especializados en fianzas con amplia experiencia en el sector afianzador y asegurador.</p>
    <p class="small">Somos reconocidos por ser un intermediario confiable, que ofrece soluciones rápidas y sin sorpresas.</p>
    <p class="small">Estamos enfocados en dar a cada cliente un servicio puntual y personalizado, siempre un paso adelante en cada trámite.</p>
    <p class="small">Nos encargamos de la suscripción y emisión de sus fianzas para que usted se concentre en su negocio.</p>
    <div class="photo" role="img" aria-label="Fotografía de edificio en construcción con grúas"></div>
  </div>

  <div class="panel clients">
    <h3>Nuestras instituciones aliadas</h3>
    <div class="partner-board">
      <div class="partner-badge"></div><div class="partner-badge"></div>
      <div class="partner-badge"></div><div class="partner-badge"></div>
      <div class="partner-badge"></div><div class="partner-badge"></div>
      <div class="partner-badge"></div><div class="partner-badge"></div>
    </div>
    <div class="curve"></div>
    <div class="contact">
      <h4>Contacto</h4>
      <div class="contact-row">
        <svg width="12" height="12" viewBox="0 0 12 12"><path d="M3 1l2 2-1 1.5c.7 1.4 1.8 2.5 3.2 3.2L8.7 6.7l2 2L9.5 10.5C5.3 10 2 6.7 1.5 2.5z" fill="#72b62f"/></svg>
        <div><b>Laura Méndez</b>contacto@talvoro.com<br>55 2140 6610</div>
      </div>
      <div class="contact-row">
        <svg width="12" height="12" viewBox="0 0 12 12"><path d="M3 1l2 2-1 1.5c.7 1.4 1.8 2.5 3.2 3.2L8.7 6.7l2 2L9.5 10.5C5.3 10 2 6.7 1.5 2.5z" fill="#72b62f"/></svg>
        <div><b>Diego Ramírez</b>fianzas@talvoro.com<br>55 2140 6624</div>
      </div>
      <div class="contact-row">
        <svg width="12" height="12" viewBox="0 0 12 12"><path d="M6 1a3.5 3.5 0 0 0-3.5 3.5C2.5 7.5 6 11 6 11s3.5-3.5 3.5-6.5A3.5 3.5 0 0 0 6 1zm0 5a1.5 1.5 0 1 1 0-3 1.5 1.5 0 0 1 0 3z" fill="#72b62f"/></svg>
        <div><b>Oficina</b>Av. Prado Norte 480<br>Ciudad de México</div>
      </div>
    </div>
    <div class="site">www.<b>talvoro</b>.com</div>
  </div>

  <div class="panel cover">
    <div class="brand"><i></i>TALVORO</div>
    <div class="brand-sub">FIANZAS Y SEGUROS</div>
    <div class="photo" role="img" aria-label="Fotografía de ingeniero con casco en obra"></div>
    <div class="tagline">Tu éxito<br><span>Nuestra Pasión</span></div>
    <div class="social"><i></i><i></i><i></i><span>/talvorobonds</span></div>
  </div>
</section>

<section class="sheet sheet--inside">
  <div class="inside-photo" role="img" aria-label="Fotografía panorámica de obra en construcción"></div>

  <div class="panel inside-col">
    <h3>Nuestra oferta de valor</h3>
    <p class="small">Servicio rápido en la suscripción y emisión de fianzas, confiable y sin sorpresas, con soluciones a la medida de cada cliente.</p>
    <p class="small">Acompañamos cada proceso de principio a fin para que usted se dedique a su negocio sin distracciones.</p>
    <h3 style="margin-top:14px">Nuestros Servicios</h3>
    <ul>
      <li>Asesoría personalizada en la contratación de fianzas.</li>
      <li>Emisión y seguimiento de pólizas.</li>
      <li>Gestión de líneas de afianzamiento.</li>
      <li>Revisión de contratos y garantías.</li>
      <li>Trámite de reclamaciones.</li>
      <li>Renovaciones puntuales y a tiempo.</li>
    </ul>
  </div>

  <div class="panel inside-col products-col">
    <h3>Productos en Fianzas</h3>
    <div class="product-row">
      <div class="icon-disc"><svg width="20" height="20" viewBox="0 0 20 20"><path d="M4 10l4 4 8-8" stroke="#fff" stroke-width="2.4" fill="none"/></svg></div>
      <ul><li>Fidelidad</li><li>Individual</li><li>Colectiva</li></ul>
    </div>
    <div class="product-row">
      <div class="icon-disc"><svg width="20" height="20" viewBox="0 0 20 20"><rect x="4" y="4" width="12" height="12" rx="2" stroke="#fff" stroke-width="2" fill="none"/></svg></div>
      <ul><li>Judiciales</li><li>Penales</li><li>No penales</li></ul>
    </div>
    <div class="product-row">
      <div class="icon-disc"><svg width="20" height="20" viewBox="0 0 20 20"><path d="M3 16h14M5 16V8l5-4 5 4v8" stroke="#fff" stroke-width="2" fill="none"/></svg></div>
      <ul><li>Administrativas</li><li>Obra y anticipo</li><li>Cumplimiento</li></ul>
    </div>
    <div class="product-row">
      <div class="icon-disc"><svg width="20" height="20" viewBox="0 0 20 20"><circle cx="10" cy="10" r="6" stroke="#fff" stroke-width="2" fill="none"/></svg></div>
      <ul><li>Crédito</li><li>Arrendamiento</li><li>Fiscales</li></ul>
    </div>
  </div>

  <div class="panel special">
    <h3>Productos Especiales</h3>
    <h4>Flujo Garantizado</h4>
    <p>Respaldo financiero para que su proyecto avance sin retrasos y con la liquidez necesaria.</p>
    <h4>Esquemas de Proveedores</h4>
    <p>Programas diseñados para afianzar a su red de proveedores con procesos ágiles y controlados.</p>
    <h4>Programa de garantías PyMEs</h4>
    <p>Soluciones a la medida para pequeñas y medianas empresas que buscan crecer con seguridad.</p>
    <div class="cta"><strong>INFORMES</strong><span>contacto@talvoro.com</span></div>
  </div>
</section>

</body>
</html>
```